African homeware retailer needs a web page design

We need a web page design for a new homeware and accessories store based in Johannesburg, South Africa. Our store carries modern African inspired items from designers that support social development and poverty alleviation initiatives. We have a particular preference for outfits that are centred on the empowerment of women.

Our business celebrates the skill, design and product of African craft and the work of designers looking to take that forward in a socially beneficial way (creating employment, developing skills, supporting local crafts people etc). We aim to carry items and inspirations from all over the African continent.

We would like to see a design that communicates African beauty and elegance without the typical tribal references that are made in reference to African craft or art.

We would like the web page to be stylish, uncomplicated, modern, captivating and appealing to the discerning customer. A similar value proposition is that of http://www.marlowtenwick.example/.

This is an e-commerce website which must be attractive to both individual buyers and design professionals so the website needs to look professional.

Here are links to some websites we like:
http://www.quenbyhollis.example/
http://www.dravelo.example/

Our logo is attached to the brief.

Target Market(s)

Our target market is female, age 20-50. However should not alienate the design conscious male customer therefore

Industry/Entity Type

E-Commerce

Requirements
Must have
• - A featured product banner which includes a photograph and text. This should be easy to edit as we will be changing the featured product regularly
- An easily expendable products section with categories. Examples of categories could be cushions, bedding, crockery etc. Should be easy to add new categories as well as new product pictures
- Home/landing page should be uncluttered
- Should use the logo and should be easy to change the logo which we have in various colour combinations. We plan to change the logo colours depending on circumstance e.g. make it red and white around Valentines day (similar to the way Vintrel frequently changes the logo on their landing page)

```html
<!DOCTYPE html>
<html lang="en">
<head>
<meta charset="utf-8">
<title>Ndalo Home — homeware &amp; accessories</title>
<link href="https://fonts.googleapis.com/css2?family=Lato:wght@300;400;700&family=Questrial&display=swap" rel="stylesheet">
<style>
  :root {
    --nav-teal: #164b58;
    --brand-green: #3aa14a;
    --light-green: #8fce8c;
    --heading-teal: #1d5a6a;
    --text-dark: #333333;
    --text-grey: #9a9a9a;
    --footer-grey: #ebebeb;
    --white: #ffffff;
  }
  * { margin: 0; padding: 0; box-sizing: border-box; }
  html, body { width: 1200px; height: 878px; overflow: hidden; }
  body {
    position: relative;
    background: var(--white);
    font-family: "Lato", sans-serif;
    color: var(--text-dark);
  }
  a { color: inherit; text-decoration: none; }

  /* Navigation */
  .main-nav {
    position: absolute; left: 0; top: 0; width: 1200px; height: 38px;
    background: var(--nav-teal);
  }
  .main-nav ul { list-style: none; }
  .main-nav li {
    position: absolute; top: 12px;
    font-size: 11.4px; color: var(--white); letter-spacing: 0.1px;
  }
  .main-nav li.is-active { color: var(--light-green); }

  /* Hero */
  .hero { position: absolute; left: 0; top: 38px; width: 1200px; height: 287px; }
  .hero-photo {
    position: absolute; left: 378px; top: 0; width: 615px; height: 287px;
    background: linear-gradient(90deg, #ffffff 0%, #e9e6df 18%, #d8d4cb 45%, #ebe8e2 75%, #ffffff 100%);
  }
  .brand {
    position: absolute; left: 178px; top: 18px; width: 215px; text-align: center;
  }
  .brand-mark {
    width: 120px; height: 120px; margin: 0 auto 28px;
    background: var(--nav-teal);
  }
  .brand-name {
    font-family: "Questrial", sans-serif;
    font-size: 30px; color: var(--brand-green); letter-spacing: 3px; line-height: 1;
  }
  .hero-rule {
    position: absolute; left: 0; top: 325px; width: 1200px; height: 4px;
    background: var(--light-green);
  }
  .side-rule {
    position: absolute; left: 1197px; top: 325px; width: 2px; height: 292px;
    background: var(--light-green);
  }

  /* Featured products */
  .section-title {
    position: absolute; left: 179px; top: 357px;
    font-family: "Questrial", sans-serif; font-size: 16.5px;
    color: var(--heading-teal); letter-spacing: 0.5px;
  }
  .carousel-arrow { position: absolute; top: 456px; width: 51px; height: 51px; }
  .carousel-arrow.prev { left: 112px; }
  .carousel-arrow.next { left: 1036px; }
  .product-card { position: absolute; top: 399px; width: 195px; }
  .product-photo { width: 195px; height: 162px; }
  .product-meta {
    display: flex; justify-content: space-between; align-items: baseline;
    margin-top: 15px;
  }
  .product-category { font-size: 13.5px; font-weight: 700; color: var(--brand-green); }
  .shop-now { font-size: 11.5px; color: var(--text-dark); display: flex; align-items: center; gap: 4px; }
  .shop-now svg { width: 5px; height: 6px; }

  /* Footer */
  .site-footer {
    position: absolute; left: 0; top: 617px; width: 1200px; height: 205px;
    background: var(--footer-grey);
  }
  .footer-col { position: absolute; top: 37px; }
  .footer-col h3 { font-size: 10.5px; font-weight: 400; color: var(--text-dark); margin-bottom: 14px; }
  .footer-col ul { list-style: none; }
  .footer-col li { font-size: 10.5px; color: var(--text-grey); height: 26.4px; }
  .newsletter { position: absolute; left: 791px; top: 33px; width: 224px; }
  .newsletter h3 { font-size: 17px; font-weight: 400; color: #4a4a4a; }
  .newsletter p { font-size: 10px; color: var(--text-grey); margin-top: 3px; }
  .email-field {
    margin-top: 12px; height: 32px; background: var(--white);
    display: flex; align-items: center; justify-content: space-between; padding: 0 10px;
    font-size: 10px; color: var(--text-grey);
  }
  .email-field svg { width: 32px; height: 16px; }
  .social-links { display: flex; gap: 12px; margin-top: 16px; list-style: none; }
  .social-links li { width: 35px; height: 35px; border-radius: 50%; }

  /* Bottom bar */
  .bottom-bar {
    position: absolute; left: 0; top: 822px; width: 1200px; height: 56px;
    background: var(--brand-green); color: var(--white);
  }
  .copyright { position: absolute; left: 178px; top: 18px; font-size: 14px; font-weight: 300; }
  .legal-links {
    position: absolute; left: 591px; top: 21px; list-style: none;
    display: flex; font-size: 10.5px;
  }
  .legal-links li + li::before { content: "|"; margin: 0 13px; }
</style>
</head>
<body>

<nav class="main-nav">
  <ul>
    <li class="is-active" style="left:198px">HOME</li>
    <li style="left:264px">FURNITURE</li>
    <li style="left:356px">CUSHIONS</li>
    <li style="left:443px">LINEN</li>
    <li style="left:506px">CERAMICS</li>
    <li style="left:593px">CUTLERY &amp; UTENSILS</li>
    <li style="left:738px">LIGHTING</li>
    <li style="left:822px">ARTWORK &amp; DECOR</li>
    <li style="left:961px">CONTACT US</li>
  </ul>
</nav>

<header class="hero">
  <div class="hero-photo" role="img" aria-label="Featured photograph of handmade white ceramic jugs"></div>
  <div class="brand">
    <div class="brand-mark"></div>
    <div class="brand-name">NDALO HOME</div>
  </div>
</header>
<div class="hero-rule"></div>
<div class="side-rule"></div>

<h2 class="section-title">FEAUTURED PRODUCTS</h2>

<svg class="carousel-arrow prev" viewBox="0 0 51 51" aria-label="Previous">
  <path d="M25.5 1 L50 25.5 L25.5 50 L1 25.5 Z" fill="none" stroke="#9a9a9a" stroke-width="1.2"/>
  <path d="M29 19 L22.5 25.5 L29 32" fill="none" stroke="#666" stroke-width="1.2"/>
</svg>
<svg class="carousel-arrow next" viewBox="0 0 51 51" aria-label="Next">
  <path d="M25.5 1 L50 25.5 L25.5 50 L1 25.5 Z" fill="none" stroke="#9a9a9a" stroke-width="1.2"/>
  <path d="M22 19 L28.5 25.5 L22 32" fill="none" stroke="#666" stroke-width="1.2"/>
</svg>

<section class="product-card" style="left:177px">
  <div class="product-photo" role="img" aria-label="Photograph of ceramic jugs" style="background:linear-gradient(135deg,#b9d3c2,#8fb1a0 60%,#6f8f80)"></div>
  <div class="product-meta"><span class="product-category">CROCKERY</span><a class="shop-now" href="#">SHOP NOW <svg viewBox="0 0 5 6"><path d="M0 0 L5 3 L0 6Z" fill="#555"/></svg></a></div>
</section>
<section class="product-card" style="left:395px">
  <div class="product-photo" role="img" aria-label="Photograph of woven pendant lights" style="background:linear-gradient(135deg,#8a8a3a,#c4622e 50%,#7a3a22)"></div>
  <div class="product-meta"><span class="product-category">LIGHTING</span><a class="shop-now" href="#">SHOP NOW <svg viewBox="0 0 5 6"><path d="M0 0 L5 3 L0 6Z" fill="#555"/></svg></a></div>
</section>
<section class="product-card" style="left:611px">
  <div class="product-photo" role="img" aria-label="Photograph of wooden candle lanterns" style="background:linear-gradient(135deg,#8fb5a8,#5a6f66 55%,#3e4a45)"></div>
  <div class="product-meta"><span class="product-category">ACCESSORIES</span><a class="shop-now" href="#">SHOP NOW <svg viewBox="0 0 5 6"><path d="M0 0 L5 3 L0 6Z" fill="#555"/></svg></a></div>
</section>
<section class="product-card" style="left:828px">
  <div class="product-photo" role="img" aria-label="Photograph of printed linen tea towels" style="background:linear-gradient(135deg,#a9c9bb,#7a9e90 50%,#3d5b52)"></div>
  <div class="product-meta"><span class="product-category">LINEN</span><a class="shop-now" href="#">SHOP NOW <svg viewBox="0 0 5 6"><path d="M0 0 L5 3 L0 6Z" fill="#555"/></svg></a></div>
</section>

<footer class="site-footer">
  <div class="footer-col" style="left:179px">
    <h3>QUICK LINKS</h3>
    <ul><li>STORE LOCATOR</li><li>MY ACCOUNT</li><li>HELP</li><li>CONTACT US</li></ul>
  </div>
  <div class="footer-col" style="left:361px">
    <h3>ABOUT NDALO HOME</h3>
    <ul><li>ABOUT US</li><li>PRESS &amp; NEWS</li><li>CAREERS</li><li>SUSTAINABILITY</li></ul>
  </div>
  <div class="footer-col" style="left:578px">
    <h3>CUSTOMER SERVICE</h3>
    <ul><li>HELP</li><li>FAQ</li><li>TERMS &amp; CONDITIONS</li><li>DISCLAIMER</li></ul>
  </div>
  <div class="newsletter">
    <h3>JOIN OUR NEWSLETTER</h3>
    <p>GET THE LATEST NEWS AND OFFERS!</p>
    <div class="email-field">
      <span>ENTER YOUR EMAIL</span>
      <svg viewBox="0 0 32 16" aria-hidden="true">
        <path d="M1 3h6M3 6h4M5 9h2" stroke="#164b58" stroke-width="1.2"/>
        <rect x="10" y="1.5" width="21" height="13" fill="none" stroke="#164b58" stroke-width="1.4"/>
        <path d="M10 1.5 L20.5 9 L31 1.5" fill="none" stroke="#164b58" stroke-width="1.4"/>
      </svg>
    </div>
    <ul class="social-links">
      <li style="background:#5b7ab0" aria-label="Social link"></li>
      <li style="background:#7fb0d3" aria-label="Social link"></li>
      <li style="background:#4cb2ad" aria-label="Social link"></li>
      <li style="background:#6fb3db" aria-label="Social link"></li>
      <li style="background:#e2574c" aria-label="Social link"></li>
    </ul>
  </div>
</footer>

<div class="bottom-bar">
  <p class="copyright">Copyright 2014 © Ndalo Home . All Rights Reserved</p>
  <ul class="legal-links">
    <li>ABOUT</li><li>ADVERTISE</li><li>ADD YOUR SITE</li><li>PRIVACY POLICY</li><li>CONTACT US</li>
  </ul>
</div>

</body>
</html>
```